New Webpage for High Class Expert Witness Services Company

We are looking for a minimalist design for a webpage that just has our logo and an entry form offer to connect with one of our Liaisons.
The entry form should just ask for Name, Email, Contact Info and Description of Project.

Company Name is: The Marlowe Crest Advisory Services

Number of Pages Required

1 page

```html
<!DOCTYPE html>
<html lang="en">
<head>
<meta charset="UTF-8">
<title>The Marlowe Crest Advisory Services — Connect with a Liaison</title>
<link href="https://fonts.googleapis.com/css2?family=Crimson+Text:wght@400;600&display=swap" rel="stylesheet">
<style>
  :root {
    --ink: #141414;
    --label: #4a4a4c;
    --field: #ffffff;
    --panel-top: #e6e6e6;
    --panel-bottom: #97979b;
    --button: #121212;
    --button-text: #ffffff;
    --photo-light: #eceeef;
    --photo-mid: #d6d5d3;
    --photo-warm: #9a8f86;
  }
  * { box-sizing: border-box; margin: 0; padding: 0; }
  html, body { width: 1200px; height: 675px; overflow: hidden; }
  body {
    position: relative;
    font-family: "Crimson Text", Georgia, serif;
    color: var(--ink);
    background: var(--panel-bottom);
  }
  .form-panel {
    position: absolute; left: 0; top: 0;
    width: 628px; height: 675px;
    background: linear-gradient(180deg, var(--panel-top) 0%, #c9c9cb 45%, var(--panel-bottom) 100%);
  }
  .brand {
    position: absolute; left: 94px; top: 25px;
    display: flex; align-items: center; gap: 12px;
  }
  .brand-square { width: 40px; height: 40px; background: var(--ink); }
  .brand-name {
    font-weight: 600; font-size: 18px; line-height: 21px;
    letter-spacing: 1.4px; text-transform: uppercase; color: var(--ink);
  }
  .headline {
    position: absolute; left: 92px; top: 145px;
    font-weight: 400; font-size: 46px; line-height: 58px;
    letter-spacing: 0.4px; text-transform: uppercase; color: var(--ink);
    white-space: nowrap;
  }
  .contact-form { position: absolute; left: 92px; top: 271px; width: 501px; }
  .row { display: flex; gap: 6px; margin-bottom: 9px; }
  .field { display: flex; flex-direction: column; width: 247px; }
  .field.wide { width: 500px; }
  .field label { font-size: 13px; line-height: 16px; color: var(--label); margin-bottom: 7px; }
  .field input, .field textarea {
    border: none; background: var(--field); height: 40px; width: 100%;
    font-family: inherit; font-size: 14px; padding: 0 10px;
  }
  .field textarea { height: 106px; resize: none; padding: 10px; }
  .submit {
    margin-top: 10px; width: 500px; height: 40px; border: none;
    background: var(--button); color: var(--button-text);
    font-family: inherit; font-size: 15px; letter-spacing: 0.5px;
  }
  .hero-photo {
    position: absolute; left: 628px; top: 0; width: 572px; height: 675px;
    background: linear-gradient(160deg, var(--photo-light) 0%, var(--photo-mid) 55%, var(--photo-warm) 100%);
  }
</style>
</head>
<body>
  <section class="form-panel">
    <div class="brand">
      <span class="brand-square"></span>
      <span class="brand-name">The Marlowe Crest<br>Advisory Services</span>
    </div>
    <h1 class="headline">Focused Protection.<br>Trusted Expertise.</h1>
    <form class="contact-form">
      <div class="row">
        <div class="field"><label for="first">First Name</label><input id="first" type="text"></div>
        <div class="field"><label for="last">Last Name</label><input id="last" type="text"></div>
      </div>
      <div class="row">
        <div class="field"><label for="email">Email</label><input id="email" type="email"></div>
        <div class="field"><label for="contact">Contact Info</label><input id="contact" type="text"></div>
      </div>
      <div class="row">
        <div class="field wide"><label for="desc">Description of Project</label><textarea id="desc"></textarea></div>
      </div>
      <button class="submit" type="submit">SUBMIT</button>
    </form>
  </section>
  <div class="hero-photo" role="img" aria-label="Photo of a smiling professional working at a laptop in a bright office, with colleagues in the background"></div>
</body>
</html>
```